Business Cards Design for the electrical wholesaler: clean bold dynamic :)

We need a business card design that would follow our latest brand guidelines. As an electrical wholesaler we want to bring a fresh look and feel into the industry. The design should be clean bold and dynamic. It should come alive with the renewed energy of our green colour. Our grey colour should keep things balanced and complement the notion of maturity and responsibility. We employ Lato as a corporate font however are not bound by this font and we’re open to interpretation here.

Target Market(s)

Electrical contractors

Industry/Entity Type

Business

Contact Information for Business Card

Logo
Name & Surname: Halyna Dorosh
Job Title: Director of Marketing
Email: halya.dorosh@quillmail.example
Cell phone: XXX.XXX.XXXX
Address: 20517 - 87 Ave. Edmonton, AB, Canada. T6K 4N8
Business Phone: 780.555.0184
Website: www.brovix.example

Font styles to use
Other font styles liked:
• Lato

Requirements
Must have
• Logo & website
Nice to have
• Brand elements - some of them you may find in the attached Brand Guidelines (e.g. three lines on the background signifying "W")

```html
<!DOCTYPE html>
<html lang="en">
<head>
<meta charset="utf-8">
<title>Brovix business cards</title>
<link href="https://fonts.googleapis.com/css2?family=Lato:wght@300;400&display=swap" rel="stylesheet">
<style>
  :root {
    --backdrop: #2e4b69;
    --card: #ffffff;
    --grey: #4a4a4c;
    --grey-soft: #6b6b6e;
    --green: #8cc63f;
    --rule: #7a7a7c;
  }
  * { box-sizing: border-box; margin: 0; padding: 0; }
  html, body { width: 1200px; height: 1000px; overflow: hidden; }
  body {
    background: var(--backdrop);
    font-family: "Lato", sans-serif;
    color: var(--grey);
    position: relative;
  }
  .card {
    position: absolute;
    width: 514px;
    height: 292px;
    background: var(--card);
  }
  .card--rounded { border-radius: 34px; }
  .card--front-round { left: 60px; top: 60px; }
  .card--back-round { left: 60px; top: 426px; }
  .card--front-square { left: 624px; top: 283px; }
  .card--back-square { left: 624px; top: 639px; }

  .brand {
    position: absolute;
    display: flex;
    align-items: center;
    gap: 12px;
    font-weight: 400;
    color: var(--grey);
    line-height: 1;
  }
  .brand__dot { border-radius: 50%; background: var(--green); flex: none; }
  .card__front .brand { left: 50%; top: 50%; transform: translate(-50%, -50%); font-size: 64px; }
  .card__front .brand__dot { width: 44px; height: 44px; }
  .card__back .brand { left: 30px; top: 28px; font-size: 44px; gap: 10px; }
  .card__back .brand__dot { width: 30px; height: 30px; }

  .person {
    position: absolute;
    right: 32px;
    top: 94px;
    text-align: right;
  }
  .person__name { font-size: 26px; font-weight: 400; color: var(--grey); line-height: 32px; }
  .person__title { font-size: 15px; font-weight: 300; color: var(--grey-soft); margin-top: 4px; }
  .divider {
    position: absolute;
    left: 28px;
    top: 142px;
    width: 292px;
    height: 1px;
    background: var(--rule);
  }
  .address {
    position: absolute;
    left: 28px;
    top: 156px;
    font-size: 15px;
    font-weight: 300;
    line-height: 19px;
    color: var(--grey);
    display: flex;
    gap: 8px;
  }
  .address svg { margin-top: 2px; flex: none; }
  .contacts {
    position: absolute;
    right: 30px;
    top: 180px;
    list-style: none;
    font-size: 17px;
    font-weight: 400;
    line-height: 24px;
    text-align: right;
  }
  .contacts li { display: flex; justify-content: flex-end; align-items: center; gap: 14px; }
  .contacts svg { width: 13px; height: 13px; flex: none; fill: var(--grey); }
  .website {
    position: absolute;
    left: 28px;
    bottom: 26px;
    font-size: 15px;
    font-weight: 300;
    color: var(--grey);
  }
</style>
</head>
<body>

  <section class="card card--rounded card--front-round card__front">
    <div class="brand"><span class="brand__dot"></span>brovix</div>
  </section>

  <section class="card card--rounded card--back-round card__back">
    <div class="brand"><span class="brand__dot"></span>brovix</div>
    <div class="person">
      <p class="person__name">Halyna Dorosh</p>
      <p class="person__title">Director of Marketing</p>
    </div>
    <div class="divider"></div>
    <p class="address">
      <svg width="11" height="14" viewBox="0 0 11 14" fill="#4a4a4c"><path d="M5.5 0A5.5 5.5 0 0 0 0 5.5C0 9.5 5.5 14 5.5 14S11 9.5 11 5.5A5.5 5.5 0 0 0 5.5 0zm0 7.6a2.1 2.1 0 1 1 0-4.2 2.1 2.1 0 0 1 0 4.2z"/></svg>
      <span>20517 - 87 Ave. Edmonton<br>AB, Canada. T6K 4N8</span>
    </p>
    <ul class="contacts">
      <li>780.555.0184 <svg viewBox="0 0 16 16"><path d="M3.6 1l2.5 2.8-1.4 2a9 9 0 0 0 5.5 5.5l2-1.4L15 12.4l-1.6 2.4C7 15 1 9 1.2 2.6z"/></svg></li>
      <li>780.555.0184 <svg viewBox="0 0 16 16"><path d="M1 6c0-3 14-3 14 0v2h-3.5V6.2h-7V8H1zM4 9h8l2 5H2z"/></svg></li>
      <li>halya.dorosh@quillmail.example <svg viewBox="0 0 16 16"><path d="M1 3h14v1.2L8 9 1 4.2zm0 2.6 7 4.8 7-4.8V13H1z"/></svg></li>
    </ul>
    <p class="website">www.brovix.example</p>
  </section>

  <section class="card card--front-square card__front">
    <div class="brand"><span class="brand__dot"></span>brovix</div>
  </section>

  <section class="card card--back-square card__back">
    <div class="brand"><span class="brand__dot"></span>brovix</div>
    <div class="person">
      <p class="person__name">Halyna Dorosh</p>
      <p class="person__title">Director of Marketing</p>
    </div>
    <div class="divider"></div>
    <p class="address">
      <svg width="11" height="14" viewBox="0 0 11 14" fill="#4a4a4c"><path d="M5.5 0A5.5 5.5 0 0 0 0 5.5C0 9.5 5.5 14 5.5 14S11 9.5 11 5.5A5.5 5.5 0 0 0 5.5 0zm0 7.6a2.1 2.1 0 1 1 0-4.2 2.1 2.1 0 0 1 0 4.2z"/></svg>
      <span>20517 - 87 Ave. Edmonton<br>AB, Canada. T6K 4N8</span>
    </p>
    <ul class="contacts">
      <li>780.555.0184 <svg viewBox="0 0 16 16"><path d="M3.6 1l2.5 2.8-1.4 2a9 9 0 0 0 5.5 5.5l2-1.4L15 12.4l-1.6 2.4C7 15 1 9 1.2 2.6z"/></svg></li>
      <li>780.555.0184 <svg viewBox="0 0 16 16"><path d="M1 6c0-3 14-3 14 0v2h-3.5V6.2h-7V8H1zM4 9h8l2 5H2z"/></svg></li>
      <li>halya.dorosh@quillmail.example <svg viewBox="0 0 16 16"><path d="M1 3h14v1.2L8 9 1 4.2zm0 2.6 7 4.8 7-4.8V13H1z"/></svg></li>
    </ul>
    <p class="website">www.brovix.example</p>
  </section>

</body>
</html>
```